"Kestrava Inc." Needs a Logo Design and Business Card

The name of the company is "Kestrava Inc."
Our Business decription, which should appear on the front of the Business Card along with the logo and business name is:
"Boutique Global Procurement and Management Services"
We offer the following SERVICES that should be listed on the back of the Business Card :
"Consultants"
"Management"
"Business Research & Development"
"Sourcing Agent"
"Distributors"
We would like to see designs that use the colors
burnt orange and,
stainless steel
Business card designs should be innovatively modern and contemporary
Telephone number and email address should be on the back of the card
The name of the firm is "Kestrava Inc.
Industry/Entity Type
Steel
Look and feel
Each slider illustrates characteristics of the customer's brand and the style your logo design should communicate.

```html
<!DOCTYPE html>
<html lang="en">
<head>
<meta charset="utf-8">
<title>Kestrava Inc. — Business Card Back</title>
<link rel="stylesheet" href="https://fonts.googleapis.com/css2?family=Quicksand:wght@300;400&display=swap">
<style>
  :root {
    --page: #ffffff;
    --card: #353535;
    --orb-dark: #292929;
    --orb-light: #4a4a4a;
    --band: #292929;
    --steel: #bdbdbd;
    --burnt-orange: #f0673a;
  }
  * { margin: 0; padding: 0; box-sizing: border-box; }
  html, body {
    width: 720px;
    height: 1200px;
    overflow: hidden;
    background: var(--page);
  }
  .card {
    position: absolute;
    left: 40px;
    top: 40px;
    width: 639px;
    height: 1120px;
    background: var(--card);
    overflow: hidden;
    font-family: "Quicksand", sans-serif;
    font-weight: 300;
  }
  .card__orbs {
    position: absolute;
    inset: 0;
  }
  .card__brand {
    position: absolute;
    right: 20px;
    top: 211px;
    font-size: 51px;
    line-height: 1;
    color: var(--steel);
    white-space: nowrap;
  }
  .services {
    list-style: none;
  }
  .services__item {
    position: absolute;
    right: 24px;
    font-size: 40px;
    line-height: 1;
    color: var(--burnt-orange);
    text-align: right;
    white-space: nowrap;
  }
  .services__item--consultants { top: 296px; }
  .services__item--management { top: 386px; }
  .services__item--research { top: 474px; line-height: 46px; }
  .services__item--sourcing { top: 609px; }
  .services__item--distributors { top: 697px; }
  .contact-band {
    position: absolute;
    left: 0;
    top: 944px;
    width: 100%;
    height: 93px;
    background: var(--band);
    color: var(--burnt-orange);
    text-align: center;
  }
  .contact-band__phone {
    position: absolute;
    left: 0;
    right: 0;
    top: 12px;
    font-size: 30px;
    line-height: 1;
    letter-spacing: 4px;
  }
  .contact-band__email {
    position: absolute;
    left: 0;
    right: 0;
    top: 55px;
    font-size: 31px;
    line-height: 1;
    letter-spacing: 3px;
  }
</style>
</head>
<body>
  <article class="card">
    <svg class="card__orbs" width="639" height="1120" viewBox="0 0 639 1120" aria-hidden="true">
      <circle cx="301" cy="308" r="243" fill="var(--orb-dark)"/>
      <circle cx="133" cy="559" r="142" fill="var(--orb-light)" fill-opacity="0.85"/>
    </svg>

    <h1 class="card__brand">KESTRAVA Inc.</h1>

    <ul class="services">
      <li class="services__item services__item--consultants">Consultants</li>
      <li class="services__item services__item--management">Management</li>
      <li class="services__item services__item--research">Research<br>&amp; Development</li>
      <li class="services__item services__item--sourcing">Sourcing Agents</li>
      <li class="services__item services__item--distributors">Distributors</li>
    </ul>

    <footer class="contact-band">
      <p class="contact-band__phone">1-888-555-0142</p>
      <p class="contact-band__email">contact-us@kestravaintl.com</p>
    </footer>
  </article>
</body>
</html>
```